Telecommunications/Power civil contractor needs business card design

Were a new telecommunications/power underground civil contractor that is looking for a new business card design. Our company colours are silver or grey and orange. Feel free to use the white background logo or the black background logo.

Target Market(s)

Local contractors, utility companies, private sector mining/energy companies, developers.

Industry/Entity Type

Telecommunications

Contact Information for Business Card

Each card will need the following info:
Persons name:
Title:
E-mail:
Phone number:
Shop Address:
Mailing Address:

Requirements
Must have
• Each card will need the following info:
• Persons name:
• Title:
• E-mail:
• Phone number:
• Shop Address:
• Mailing Address:

```html
<!DOCTYPE html>
<html lang="en">
<head>
<meta charset="utf-8">
<title>Trenchline Contracting Inc — Business Card</title>
<link href="https://fonts.googleapis.com/css2?family=Open+Sans:wght@400;600;700;800&display=swap" rel="stylesheet">
<style>
  :root {
    --backdrop: #e9e6e2;
    --card-white: #ffffff;
    --brand-orange: #f15a24;
    --brand-grey: #5f5f5f;
    --logo-grey: #8a8a8a;
    --card-black: #0d0d0d;
    --text-light: #ffffff;
  }
  * { box-sizing: border-box; margin: 0; padding: 0; }
  html, body {
    width: 1200px; height: 675px; overflow: hidden;
    background: var(--backdrop);
    font-family: "Open Sans", Arial, sans-serif;
  }
  .canvas {
    position: relative; width: 1200px; height: 675px;
    display: flex; align-items: center; justify-content: center; gap: 60px;
  }
  .card {
    position: relative; width: 520px; height: 300px;
    border-radius: 24px; overflow: hidden;
    box-shadow: 0 6px 18px rgba(0,0,0,0.18);
  }

  /* Front */
  .card-front { background: var(--card-white); }
  .front-bands { position: absolute; inset: 0; }
  .front-logo {
    position: absolute; left: 38px; top: 34px;
    display: flex; align-items: center; gap: 10px;
  }
  .logo-dot {
    width: 34px; height: 34px; border-radius: 50%;
    background: var(--brand-orange); flex: none;
  }
  .logo-name {
    font-weight: 800; font-size: 15px; line-height: 1.1;
    letter-spacing: 0.04em; color: var(--brand-orange);
    text-transform: uppercase; width: 150px;
  }
  .contact-list {
    position: absolute; left: 38px; top: 138px;
    list-style: none; color: var(--text-light);
    font-size: 12.5px; line-height: 1.55;
  }
  .contact-list li { display: flex; align-items: center; gap: 8px; }
  .contact-list .no-icon { padding-left: 22px; }
  .contact-list svg { width: 14px; height: 14px; flex: none; }
  .person {
    position: absolute; right: 24px; top: 168px; text-align: right;
  }
  .person-name {
    font-weight: 700; font-size: 14px; color: var(--text-light);
    text-transform: uppercase; letter-spacing: 0.02em;
  }
  .person-title {
    margin-top: 10px; font-size: 13px; color: var(--text-light);
  }

  /* Back */
  .card-back {
    background: var(--card-white); padding: 12px;
  }
  .back-panel {
    width: 100%; height: 100%; border-radius: 16px;
    background: var(--card-black);
    display: flex; flex-direction: column; align-items: center; justify-content: center; gap: 14px;
  }
  .back-dot {
    width: 70px; height: 70px; border-radius: 50%;
    background: var(--brand-orange);
  }
  .back-name {
    font-weight: 800; font-size: 26px; line-height: 1.15;
    letter-spacing: 0.05em; color: var(--brand-orange);
    text-transform: uppercase; text-align: center;
  }
</style>
</head>
<body>
<main class="canvas">

  <section class="card card-front" aria-label="Business card front">
    <svg class="front-bands" viewBox="0 0 520 300" preserveAspectRatio="none" aria-hidden="true">
      <polygon points="0,108 290,108 320,146 520,146 520,152 316,152 286,114 0,114" fill="var(--brand-grey)"/>
      <polygon points="0,118 284,118 314,158 520,158 520,300 0,300" fill="var(--brand-orange)"/>
      <polygon points="316,152 520,152 520,190 336,190" fill="var(--brand-grey)"/>
    </svg>

    <div class="front-logo">
      <span class="logo-dot"></span>
      <span class="logo-name">Trenchline Contracting Inc</span>
    </div>

    <ul class="contact-list">
      <li class="no-icon">N. 4 Sample Road,</li>
      <li class="no-icon">Suite 210, Ridgeview, WA 55555</li>
      <li>
        <svg viewBox="0 0 24 24" aria-hidden="true"><path fill="#fff" d="M6.6 10.8a15.1 15.1 0 0 0 6.6 6.6l2.2-2.2a1 1 0 0 1 1-.25 11.4 11.4 0 0 0 3.6.57 1 1 0 0 1 1 1V20a1 1 0 0 1-1 1A17 17 0 0 1 3 4a1 1 0 0 1 1-1h3.5a1 1 0 0 1 1 1c0 1.25.2 2.45.57 3.57a1 1 0 0 1-.25 1z"/></svg>
        555.010.2468
      </li>
      <li>
        <svg viewBox="0 0 24 24" aria-hidden="true"><path fill="#fff" d="M3 5h18a1 1 0 0 1 1 1v12a1 1 0 0 1-1 1H3a1 1 0 0 1-1-1V6a1 1 0 0 1 1-1zm9 7.2L4 7.5V8l8 5 8-5v-.5z"/></svg>
        info@trenchlinecontracting.com
      </li>
    </ul>

    <div class="person">
      <p class="person-name">Morgan Hale</p>
      <p class="person-title">Managing Director</p>
    </div>
  </section>

  <section class="card card-back" aria-label="Business card back">
    <div class="back-panel">
      <span class="back-dot"></span>
      <p class="back-name">Trenchline<br>Contracting Inc</p>
    </div>
  </section>

</main>
</body>
</html>
```